Quote Cards With KB May 2025 for Instagram

I would like to put these quotes over one of the pictures attached; Instagram (new size: 4:5 (1080 x 1350 pixels) One Quote per picture, and I want the quote to be bold or easy to read as well. I provided a few reference graphics that I really like as examples below. In very small letters at the bottom add @KBHarlowOnline

All of the pictures are attached; you can pick any photo and add one quote to it; but no stock photography

```html
<!DOCTYPE html>
<html lang="en">
<head>
<meta charset="UTF-8">
<title>Quote Card – KB</title>
<link href="https://fonts.googleapis.com/css2?family=Bebas+Neue&family=Oswald:wght@400&display=swap" rel="stylesheet">
<style>
  :root {
    --pink-hot: #f0509a;
    --pink-soft: #e9a6cf;
    --pink-mist: #f4c6e2;
    --mauve: #b86a9c;
    --panel-top: rgba(70, 20, 45, 0.78);
    --panel-mid: rgba(35, 10, 25, 0.85);
    --panel-bottom: rgba(10, 4, 8, 0.95);
    --ink: #ffffff;
    --floor: #1a0a14;
  }
  * { margin: 0; padding: 0; box-sizing: border-box; }
  html, body { width: 960px; height: 1200px; overflow: hidden; background: #000; }
  .card {
    position: relative;
    width: 960px;
    height: 1200px;
    overflow: hidden;
    font-family: "Bebas Neue", "Oswald", sans-serif;
    color: var(--ink);
  }
  .photo-backdrop {
    position: absolute;
    inset: 0;
    background:
      radial-gradient(ellipse 60% 55% at 78% 40%, var(--pink-mist) 0%, transparent 70%),
      linear-gradient(180deg, var(--pink-soft) 0%, var(--mauve) 55%, var(--floor) 100%),
      linear-gradient(90deg, var(--pink-hot) 0%, var(--pink-soft) 100%);
  }
  .photo-portrait {
    position: absolute;
    left: 660px;
    top: 125px;
    width: 250px;
    height: 1075px;
    border-radius: 120px 120px 20px 20px;
    background: linear-gradient(180deg, #c56e9e 0%, #d27bab 40%, #c2709f 100%);
    opacity: 0.85;
  }
  .quote-panel {
    position: absolute;
    left: 36px;
    top: 0;
    width: 587px;
    height: 1200px;
    background: linear-gradient(180deg, var(--panel-top) 0%, var(--panel-mid) 55%, var(--panel-bottom) 100%);
  }
  .quote-line {
    position: absolute;
    left: 73px;
    text-transform: uppercase;
    white-space: nowrap;
  }
  .headline {
    top: 108px;
    font-size: 86px;
    line-height: 93px;
    letter-spacing: 0.5px;
  }
  .promise {
    top: 428px;
    font-size: 86px;
    line-height: 100px;
    letter-spacing: 0.5px;
  }
  .callout {
    left: 64px;
    top: 885px;
    font-size: 128px;
    line-height: 1;
    letter-spacing: 0.5px;
  }
  .handle {
    position: absolute;
    left: 73px;
    top: 1104px;
    font-size: 31px;
    line-height: 1;
    letter-spacing: 0.3px;
  }
</style>
</head>
<body>
  <div class="card">
    <div class="photo-backdrop" role="img" aria-label="Pink stage backdrop with soft curtains and lights"></div>
    <div class="photo-portrait" role="img" aria-label="Photo of KB smiling in a pink sparkling bodysuit, hand on hip"></div>

    <div class="quote-panel"></div>

    <p class="quote-line headline">This 90-day plan<br>helped women<br>over 40 slim down</p>
    <p class="quote-line promise">Get a tiny waist<br>and feel sexy<br>again.</p>
    <p class="quote-line callout">You’re next.</p>

    <p class="handle">@KBHARLOWONLINE</p>
  </div>
</body>
</html>
```